Systems and Technology Consultants - Website

Design & Build a website for a new company which operates in the Systems and Technology space for Transportation, Government and Commercial sectors.

Overall design should be minimalist in nature.
Should also have a feed that provides news and event updates on the main page.
Logo has already been awarded and should be incorporated into the site.

We like the overall layout, functionality and simplicity of the below sites. Submitted designs could be similar to or a combination of the aspects on these sites, or perhaps a whole different concept - we are open to new ideas.
Norvique.com
Teblo.it

Update 1 Dated 27 May 2014

All I am moving away from the Teblo.it website and would like it to be more aligned with Norvique.com not only in layout but in functionality. I will be extending the deadline of this design brief for two weeks to incorporate additional requirements and will add addtional funding to the project.

Apologies for not having more information available to provide but with so many submissions its getting confusing.

Thanks Derek

Please note that the brief has been updated and the deadline has been extended.

Important: We will need two language versions of the website, English and Arabic; the website is hosted on HostPelican

Hello All, Thank you for your submissions. We have narrowed it down to the final 6 designers and I just wanted to take a moment and provide a bit of feedback regarding the concepts that we like and the modifications we are looking for. First, let me mention some of the design functions we like. - At the top of the homepage we really like the "region" or "language" tab so that the website can be viewed in both English and Arabic. - We like the homepage to have clear color variation so that the different sections of the homepage are distinct. Additionally, we like the bottom portion of the homepage to be in red. We feel that draws attention to our contact information. Again, we would like the colors to integrate black, gray-scale, red, etc. - Having a search tab at the top of the home page, or integrated into the main image, so that the site is easy to navigate. - We especially like the main image to have the scrolling tabs at the bottom so it is easy to browse the services offered (Consultancy, Solutions Architecture, Masters Systems Integration, Independent Design Review). - In regards to the services offered tab we really like the idea that a few people presented that have the outside of our logo with an icon in the middle of consultancy, solutions, etc., etc. Secondly, as mentioned in our brief we really enjoy the design of norvique site. Specially, we enjoy the strong iconic images they use, the way the tabs at the top scroll easily, and contact us page that generates an email. Lastly, I've included some photos of the concept we have been working on. What we are trying to demonstrate is how our company offers a range of services that are essentially linked together. We provide individual services that when combined present the full service package. We would like this concept to be integrated into the over concept of our website. Please feel free to ask for clarification of any of the above points or contact us if you have any additional questions. We appreciate all of your hard work and are very excited to see the updated designs. Best, Marta Vennick Quelbrant Senior Program Manager marta.vennick@quelbrant-example.com

Industry/Entity Type

Government

Font styles to use
Serif
Sans Serif

Requirements
Must have
• Must work on/adapt to various/mobile devices (responsive)
Must be simple and straightforward
Colors should be in line/matching with logo
2 language versions: English and Arabic (no Thai)
Services should be the first group/row of items after/below the main image
Note: the website will be hosted by hostpelican
Nice to have
• Submit feedback form
What's New section
The banner at the bottom of the site should not be too large; we would like a narrow one more
It would be nice if the header/top banner (with Home, About, etc. tabs) could stay in place as you scroll down (like Norvique and Chatterloop)
We will likely only use one image with a Company slogan on the Home page rather than a carousel of images to rotate through
Should not have
• This is the existing website: http://www.quelbrant-example.org
We do not like the animation, the way the banner icons/titles bounce
Not simple enough, we don't like the functionality or how pages load so slowly
We do not like the logo centered - it should be at the left
The banner and its tabs should not be towards the right, we would like them to be centered, to go all the way across and to be below the logo

```html
<!DOCTYPE html>
<html lang="en">
<head>
<meta charset="utf-8">
<title>Quelbrant — Systems and Technology Consultants</title>
<link rel="stylesheet" href="https://fonts.googleapis.com/css2?family=Open+Sans:wght@400;600;700&family=Raleway:wght@400;600;700&display=swap">
<style>
:root{
  --red:#e01a22;
  --ink:#222;
  --text:#555;
  --muted:#8a8a8a;
  --paper:#f1f0eb;
  --white:#fff;
  --footer:#2b2b2b;
  --footer-deep:#1d1d1d;
  --line:#d8d6cf;
}
*{box-sizing:border-box;margin:0;padding:0}
html,body{width:674px;height:1200px;overflow:hidden;background:var(--white)}
body{position:relative;font-family:"Open Sans",Arial,sans-serif;color:var(--ink)}
a{color:inherit;text-decoration:none}
.abs{position:absolute}

/* header */
.site-header{position:absolute;left:0;top:0;width:674px;height:81px;background:var(--white)}
.brand{position:absolute;left:62px;top:28px;display:flex;align-items:center;gap:6px;font-family:"Raleway",sans-serif;font-weight:700;font-size:17px;color:var(--red);letter-spacing:.5px}
.brand-mark{width:12px;height:12px;background:var(--red)}
.call{position:absolute;right:64px;top:6px;font-size:10px;color:#333;display:flex;align-items:center;gap:3px}
.call strong{font-weight:400}
.social{position:absolute;right:64px;top:22px;display:flex;gap:2px}
.social span{width:17px;height:16px;background:#c9c9c9}
.main-nav{position:absolute;right:64px;top:51px;display:flex;gap:28px;font-size:8px;color:#222}
.main-nav a{position:relative;padding-bottom:6px}
.main-nav .active{color:var(--red);font-weight:600}
.main-nav .active::after{content:"";position:absolute;left:-7px;right:-7px;bottom:-3px;height:2px;background:var(--red)}

/* hero */
.hero{position:absolute;left:0;top:81px;width:674px;height:281px;background:radial-gradient(ellipse at 62% 40%,#8a8d92 0%,#4a4c50 35%,#1c1d1f 75%)}
.hero-photo{position:absolute;left:290px;top:0;width:384px;height:281px;background:radial-gradient(circle at 45% 55%,rgba(120,210,235,.55) 0%,rgba(60,120,150,.25) 30%,rgba(0,0,0,0) 60%)}
.hero-title{position:absolute;left:63px;top:83px;width:250px;font-family:"Raleway",sans-serif;font-size:15.5px;line-height:20px;color:var(--white)}
.hero-title strong{font-weight:700}
.hero-cta{position:absolute;left:63px;top:156px;height:24px;width:143px;border-radius:12px;background:#1b1b1b;color:var(--white);font-size:9px;display:flex;align-items:center;padding-left:10px;gap:3px;font-family:"Raleway",sans-serif}
.hero-cta b{font-weight:700}
.hero-cta i{position:absolute;right:5px;top:5px;width:14px;height:14px;border-radius:50%;background:var(--white)}

/* welcome */
.welcome{position:absolute;left:0;top:362px;width:674px;height:173px;background:var(--paper)}
.welcome::before{content:"";position:absolute;left:20px;right:20px;top:0;height:8px;background:radial-gradient(ellipse at 50% 0,rgba(0,0,0,.22),rgba(0,0,0,0) 70%)}
.welcome-rule{position:absolute;left:0;right:0;top:46px;height:1px;background:var(--line)}
.welcome-title{position:absolute;left:0;right:0;top:33px;text-align:center}
.welcome-title span{background:var(--paper);padding:0 10px;font-family:"Raleway",sans-serif;font-size:19px;color:#222}
.welcome-title b{color:var(--red);font-weight:700}
.dot{position:absolute;top:41px;width:11px;height:11px;border-radius:50%;background:#c4c4c4}
.welcome p{position:absolute;left:105px;width:464px;top:68px;text-align:center;font-size:7.3px;line-height:13.5px;color:#444}
.btn-dark{position:absolute;left:305px;top:125px;width:64px;height:20px;background:#222;color:var(--white);font-size:7.5px;font-weight:600;display:flex;align-items:center;justify-content:center}

/* services */
.services{position:absolute;left:0;top:535px;width:674px;height:265px;background:var(--white)}
.services h2{position:absolute;left:0;right:0;top:28px;text-align:center;font-weight:400;font-size:13px;font-family:"Open Sans",sans-serif}
.service{position:absolute;top:58px;width:170px;text-align:center}
.service-icon{width:52px;height:52px;margin:0 auto;border:3px solid var(--red);border-radius:50%}
.service h3{margin-top:14px;font-weight:400;font-size:10px}
.service p{margin-top:9px;font-size:6.8px;line-height:11.3px;color:var(--muted)}
.service .more{display:inline-block;margin-top:14px;width:48px;height:16px;line-height:14px;font-size:7px;border:1px solid #333;color:#222}
.service .more.primary{background:var(--red);border-color:var(--red);color:var(--white)}
.col-split{position:absolute;top:55px;width:1px;height:170px;background:linear-gradient(#fff,#ececec,#fff)}

/* feeds */
.feeds{position:absolute;left:0;top:800px;width:674px;height:228px;background:var(--paper);border-top:1px solid #e8e6e0}
.feed-head{position:absolute;font-size:12px;color:#222}
.view-all{position:absolute;font-size:6.5px;color:var(--red)}
.feed-rule{position:absolute;height:1px;background:var(--line)}
.article{position:absolute;left:68px;width:300px;height:50px}
.article .thumb{position:absolute;left:0;top:0;width:61px;height:49px;background:linear-gradient(135deg,#6f8aa3,#2c3a48)}
.article h4,.news-item h4{font-weight:400;font-size:9px;color:#222}
.article h4{position:absolute;left:69px;top:0}
.article p{position:absolute;left:69px;top:17px;width:220px;font-size:7px;line-height:11px;color:var(--muted)}
.feed-divider{position:absolute;left:386px;top:20px;width:1px;height:190px;background:#dddbd4}
.news-item{position:absolute;left:400px;width:206px;height:52px;border-bottom:1px solid #e0ded7}
.news-date{position:absolute;left:7px;top:2px;width:30px;text-align:center;line-height:15px}
.news-date b{display:block;color:var(--red);font-size:15px;font-weight:600}
.news-date span{font-size:12px;color:#111}
.news-item h4{position:absolute;left:39px;top:0}
.news-item p{position:absolute;left:39px;top:15px;width:150px;font-size:7px;line-height:11px;color:var(--muted)}

/* footer */
.site-footer{position:absolute;left:0;top:1028px;width:674px;height:147px;background:var(--footer);border-top:3px solid var(--red)}
.footer-brand{position:absolute;left:68px;top:30px;display:flex;align-items:center;gap:6px;font-family:"Raleway",sans-serif;font-weight:700;font-size:16px;color:var(--white)}
.footer-brand i{width:11px;height:11px;background:var(--white)}
.footer-about{position:absolute;left:64px;top:86px;width:125px;font-size:7px;line-height:11px;color:#888}
.footer-col h5{position:absolute;font-weight:400;font-size:10px;color:#eee}
.footer-sep{position:absolute;top:20px;width:1px;height:120px;background:#3c3c3c}
.sitemap{position:absolute;left:233px;top:44px;list-style:none;font-size:7px;line-height:8.7px;color:#ddd}
.contact{position:absolute;left:339px;top:44px;font-size:7px;line-height:10px;color:#999}
.map{position:absolute;left:467px;top:40px;width:145px;height:93px;background:linear-gradient(135deg,#ecebe4,#e2e0d4 55%,#f1e9a6)}
.footer-bar{position:absolute;left:0;top:1175px;width:674px;height:25px;background:var(--footer-deep);color:#ccc;font-size:7px;text-align:center;line-height:25px}
</style>
</head>
<body>

<header class="site-header">
  <div class="brand"><span class="brand-mark"></span>Quelbrant</div>
  <div class="call">
    <svg width="8" height="10" viewBox="0 0 8 10"><path d="M1.5 0.5 L3 0.5 L3.6 2.8 L2.6 3.6 Q3.4 5.8 5 7 L6 6.2 L7.6 7.4 L7.2 9 Q3.5 9.5 1 4 Q0.6 1.5 1.5 .5Z" fill="#e01a22"/></svg>
    Call Us : <strong>+100 555 0190</strong>
  </div>
  <div class="social" aria-label="Social links"><span></span><span></span><span></span><span></span><span></span><span></span></div>
  <nav class="main-nav">
    <a class="active">HOME</a><a>Business Units</a><a>Services</a><a>About Us</a><a>Locations</a><a>Contact Us</a>
  </nav>
</header>

<section class="hero">
  <div class="hero-photo" role="img" aria-label="Businessman in a suit touching glowing digital interface circles"></div>
  <h1 class="hero-title"><strong>Quelbrant</strong> Specializes in deliver-ing Quality Professional Services and Technical Projects .</h1>
  <a class="hero-cta">LEARN MORE <b>ABOUT US</b><i><svg width="14" height="14" viewBox="0 0 14 14"><path d="M4 7h5M7 4.5 9.5 7 7 9.5" stroke="#e01a22" stroke-width="1.6" fill="none"/></svg></i></a>
</section>

<section class="welcome">
  <div class="welcome-rule"></div>
  <span class="dot" style="left:212px"></span>
  <span class="dot" style="left:455px"></span>
  <h2 class="welcome-title"><span>Welcome to <b>QUELBRANT</b></span></h2>
  <p>We &nbsp;specializes in delivering quality professional services and technical projects that support larger business goals. &nbsp;systems are tools that support a greater business function and need. we understand that most technical projects are conceptualized to support a larger vision with actual business goals in mind and ensure that all of our professional</p>
  <a class="btn-dark">Read More</a>
</section>

<section class="services">
  <h2>Our Services</h2>
  <div class="col-split" style="left:250px"></div>
  <div class="col-split" style="left:432px"></div>
  <article class="service" style="left:70px">
    <div class="service-icon"></div>
    <h3>Consulting</h3>
    <p>Lorem Ipsum is simply dummy text of the printing and typesetting industry. Lorem Ipsum has been the industry's standard dummy text ever since the 1500s.</p>
    <a class="more primary">Read More</a>
  </article>
  <article class="service" style="left:252px">
    <div class="service-icon"></div>
    <h3>Engineering</h3>
    <p>Lorem Ipsum is simply dummy text of the printing and typesetting industry. Lorem Ipsum has been the industry's standard dummy text ever since the 1500s.</p>
    <a class="more">Read More</a>
  </article>
  <article class="service" style="left:433px">
    <div class="service-icon"></div>
    <h3>Construction</h3>
    <p>Lorem Ipsum is simply dummy text of the printing and typesetting industry. Lorem Ipsum has been the industry's standard dummy text ever since the 1500s.</p>
    <a class="more">Read More</a>
  </article>
</section>

<section class="feeds">
  <h3 class="feed-head" style="left:69px;top:17px">Articles</h3>
  <a class="view-all" style="left:343px;top:25px">View All</a>
  <div class="feed-rule" style="left:68px;top:33px;width:300px"></div>

  <article class="article" style="top:41px">
    <div class="thumb" role="img" aria-label="Two business colleagues at a desk"></div>
    <h4>Lorem ipsum dolor sit amet, consectetur</h4>
    <p>Lorem Ipsum is simply dummy text of the printing and typesetting industry.</p>
  </article>
  <article class="article" style="top:97px">
    <div class="thumb" role="img" aria-label="Hand touching a digital interface"></div>
    <h4>Lorem ipsum dolor sit amet, consectetur</h4>
    <p>Lorem Ipsum is simply dummy text of the printing and typesetting industry.</p>
  </article>
  <article class="article" style="top:154px">
    <div class="thumb" role="img" aria-label="Businessman pressing a glowing screen"></div>
    <h4>Lorem ipsum dolor sit amet, consectetur</h4>
    <p>Lorem Ipsum is simply dummy text of the printing and typesetting industry. Lorem Ipsum has been the industry's standard dummy text.</p>
  </article>

  <div class="feed-divider"></div>

  <h3 class="feed-head" style="left:403px;top:17px">News</h3>
  <a class="view-all" style="left:579px;top:25px">View All</a>
  <div class="feed-rule" style="left:400px;top:33px;width:206px"></div>

  <article class="news-item" style="top:42px">
    <div class="news-date"><b>27</b><span>Feb</span></div>
    <h4>Lorem ipsum dolor sit amet,</h4>
    <p>Lorem Ipsum is simply dummy text of the printing and typesetting industry.</p>
  </article>
  <article class="news-item" style="top:95px">
    <div class="news-date"><b>23</b><span>Feb</span></div>
    <h4>Lorem ipsum dolor sit amet,</h4>
    <p>Lorem Ipsum is simply dummy text of the printing and typesetting industry.</p>
  </article>
  <article class="news-item" style="top:148px">
    <div class="news-date"><b>22</b><span>Feb</span></div>
    <h4>Lorem ipsum dolor sit amet,</h4>
    <p>Lorem Ipsum is simply dummy text of the printing and typesetting industry.</p>
  </article>
</section>

<footer class="site-footer">
  <div class="footer-brand"><i></i>Quelbrant</div>
  <p class="footer-about">Lorem Ipsum is simply dummy text of the printing and typesetting industry.</p>
  <div class="footer-sep" style="left:202px"></div>
  <div class="footer-sep" style="left:312px"></div>
  <div class="footer-col">
    <h5 style="left:233px;top:22px">Site Map</h5>
    <ul class="sitemap"><li>Home</li><li>Business Units</li><li>Services</li><li>About Us</li><li>Locations</li><li>Contact Us</li></ul>
  </div>
  <div class="footer-col">
    <h5 style="left:339px;top:22px">Get in touch</h5>
    <div class="contact">Toll-Free: 1-800-555-0147<br>Local: 555-0182-3301<br>Fax: 555-0182-3302</div>
  </div>
  <div class="footer-col">
    <h5 style="left:472px;top:22px">Map</h5>
    <div class="map" role="img" aria-label="Street map of the office location"></div>
  </div>
</footer>
<div class="footer-bar">Copyright © 2014 Quelbrant . All rights reserved.</div>

</body>
</html>
```